Brochure for a new technology in mineral processing industry

We require a rush design for a brochure for an upcoming conference on 8th December. It needs to comply with our logo colours and web site (www.krelvantech.com.au). The attached is a mockup (not very creative) that should be used as a guide only. A word version is available upon request. The design should be aligned with a science and engineering based organisation and not be too busy in its design. Looking for classic but simple lines. Photos loaded up should be used at the designers discretion to enhance look.

Target Market(s)

Brochure to be used to market to mining industry.

Industry/Entity Type

Mining

Requirements
Must have
• The brochure must have simple lines - not to be busy. Colours to match logo and corporate colours and website branding.
Nice to have
• Themes that we feel would be nice to bring through:
• 1. Step Change/modern/innovation
• 2. Clever science being commercialised
• 3. Mining Industry
Should not have
• Not too busy. Arty perspectives.

```html
<!DOCTYPE html>
<html lang="en">
<head>
<meta charset="utf-8">
<title>Krelvan Technologies – Research Backing</title>
<link href="https://fonts.googleapis.com/css2?family=Montserrat:wght@300;400;700;800&display=swap" rel="stylesheet">
<style>
  :root {
    --brand-blue: #3a5fae;
    --brand-blue-deep: #2f52a0;
    --brand-orange: #c27a36;
    --brand-orange-light: #e0a060;
    --ink: #2e2e2e;
    --paper: #ffffff;
  }
  html, body {
    margin: 0;
    padding: 0;
    overflow: hidden;
    background: var(--paper);
  }
  .page {
    position: relative;
    width: 848px;
    height: 1200px;
    overflow: hidden;
    background: var(--paper);
    font-family: "Montserrat", sans-serif;
    color: var(--ink);
  }
  .hero-art {
    position: absolute;
    left: 0;
    top: 0;
    width: 848px;
    height: 800px;
  }
  .research-section {
    position: absolute;
    left: 0;
    top: 760px;
    width: 848px;
    text-align: center;
  }
  .research-heading {
    margin: 0;
    font-size: 14.5px;
    font-weight: 700;
    letter-spacing: 0.3px;
    color: var(--brand-blue);
  }
  .research-copy {
    margin: 18px auto 0;
    width: 640px;
    font-size: 15.5px;
    font-weight: 300;
    line-height: 20px;
    color: var(--ink);
  }
  .company-block {
    position: absolute;
    left: 0;
    top: 1005px;
    width: 848px;
    text-align: center;
  }
  .company-name {
    display: inline-flex;
    align-items: center;
    gap: 12px;
    font-size: 22px;
    font-weight: 800;
    line-height: 24px;
    color: var(--brand-blue);
    text-align: left;
  }
  .company-mark {
    width: 44px;
    height: 44px;
    background: var(--brand-orange);
  }
  .company-address {
    margin: 18px 0 0;
    font-size: 11px;
    font-weight: 400;
    line-height: 14.5px;
    font-style: normal;
  }
  .company-web {
    margin: 12px 0 0;
    font-size: 11px;
    font-weight: 400;
  }
</style>
</head>
<body>
<main class="page">
  <svg class="hero-art" viewBox="0 0 848 800" xmlns="http://www.w3.org/2000/svg">
    <defs>
      <linearGradient id="buildingTone" x1="0" y1="0" x2="1" y2="1">
        <stop offset="0" stop-color="#cfd6de"/>
        <stop offset="0.5" stop-color="#9aa3ad"/>
        <stop offset="1" stop-color="#e6e8ea"/>
      </linearGradient>
      <linearGradient id="ringTone" x1="0" y1="0" x2="1" y2="1">
        <stop offset="0" stop-color="var(--brand-orange-light)"/>
        <stop offset="1" stop-color="var(--brand-orange)"/>
      </linearGradient>
      <radialGradient id="flaskTone" cx="0.5" cy="0.5" r="0.6">
        <stop offset="0" stop-color="#5a8fd8"/>
        <stop offset="1" stop-color="#6f6f70"/>
      </radialGradient>
      <radialGradient id="reactorTone" cx="0.5" cy="0.55" r="0.6">
        <stop offset="0" stop-color="#3a3a40"/>
        <stop offset="1" stop-color="#c9c9c4"/>
      </radialGradient>
      <radialGradient id="oreTone" cx="0.4" cy="0.6" r="0.6">
        <stop offset="0" stop-color="#e8eef0"/>
        <stop offset="1" stop-color="#b86a36"/>
      </radialGradient>
    </defs>

    <rect class="backdrop" x="0" y="0" width="848" height="800" fill="var(--brand-blue)"/>

    <path class="building-photo" role="img" aria-label="Photo of a modern research centre building with grey louvred facade under a blue sky"
          d="M0 0 H807 C760 110 690 230 608 300 C560 345 520 380 470 400 C400 440 320 470 240 482 C150 494 60 497 0 499 Z"
          fill="url(#buildingTone)"/>
    <path class="accent-curve" d="M0 499 C60 497 150 494 240 482 C320 470 400 440 470 400 C520 380 560 345 608 300 C690 230 760 110 807 0"
          fill="none" stroke="var(--brand-orange)" stroke-width="5"/>

    <path class="white-sweep" d="M0 795 C120 640 300 600 520 575 C680 560 780 556 848 553 V800 H0 Z" fill="var(--paper)"/>

    <g class="photo-ring">
      <circle cx="703" cy="242" r="110" fill="url(#ringTone)" stroke="#8a8a8a" stroke-width="2"/>
      <circle role="img" aria-label="Photo of laboratory flasks holding blue solution" cx="703" cy="242" r="99" fill="url(#flaskTone)"/>
    </g>
    <g class="photo-ring">
      <circle cx="472" cy="461" r="107" fill="url(#ringTone)" stroke="#8a8a8a" stroke-width="2"/>
      <circle role="img" aria-label="Photo of a laboratory leaching reactor on a bench" cx="472" cy="461" r="96" fill="url(#reactorTone)"/>
    </g>
    <g class="photo-ring">
      <circle cx="164" cy="582" r="110" fill="url(#ringTone)" stroke="#8a8a8a" stroke-width="2"/>
      <circle role="img" aria-label="Photo of orange ore rock beside frothing process water" cx="164" cy="582" r="99" fill="url(#oreTone)"/>
    </g>
  </svg>

  <section class="research-section">
    <h2 class="research-heading">OUR TECHNOLOGY IS BACKED BY A LEADING RESEARCH GROUP</h2>
    <p class="research-copy">Krelvan Technologies (KT), through its collaboration and commercialisation agreement with Westbrook University, has the backing and support of a leading minerals research group continuing to undertake fundamental research into Glycine leaching.</p>
  </section>

  <footer class="company-block">
    <div class="company-name">
      <span class="company-mark"></span>
      <span>KRELVAN<br>TECHNOLOGIES</span>
    </div>
    <address class="company-address">Coastal Minerals Research Hub<br>14 Harlow Street, Bayview<br>Western Australia 6158</address>
    <p class="company-web">www.krelvantech.com.au</p>
  </footer>
</main>
</body>
</html>
```